BOLD & MINIMALIST DESIGN NEEDED

We want a very bold but minimalistic business card design that is impactful and utilizes both sides of the business card. Our current logo is included for your use.

We want bold fonts and good use of negative space. We don't want the logo to overpower the design.

Target Market(s)

Professionals who are building new commercial buildings.

Industry/Entity Type

Construction

Contact Information for Business Card

Name, Title, email, office phone, cell phone, website

Font styles to use
Serif
Sans Serif

Requirements
Must have
• Bold design!

```html
<!DOCTYPE html>
<html lang="en">
<head>
<meta charset="utf-8">
<title>Ridgeline — Business Card</title>
<link href="https://fonts.googleapis.com/css2?family=Montserrat:wght@500;700;800&display=swap" rel="stylesheet">
<style>
  :root {
    --backdrop: #1c1c1c;
    --card-white: #ffffff;
    --brand-green: #84c441;
    --ink: #111111;
    --text: #2e2e2e;
  }
  * { margin: 0; padding: 0; box-sizing: border-box; }
  html, body {
    width: 1200px; height: 1059px; overflow: hidden;
    background: var(--backdrop);
    font-family: "Montserrat", Arial, sans-serif;
  }
  .stage { position: relative; width: 1200px; height: 1059px; }
  .card { position: absolute; border-radius: 20px; overflow: hidden; }
  .card--front { left: 256px; top: 89px; width: 689px; height: 393px; background: var(--card-white); }
  .card--back { left: 253px; top: 545px; width: 695px; height: 398px; background: var(--brand-green); }

  .wordmark {
    position: absolute; display: flex; align-items: center; justify-content: center;
    font-weight: 800; line-height: 1; white-space: nowrap;
  }
  .wordmark--front { left: 20px; width: 368px; top: 170px; height: 52px; gap: 12px; color: var(--ink); font-size: 46px; }
  .wordmark--front .mark-square { width: 30px; height: 30px; background: var(--ink); flex: none; }
  .wordmark--back { left: 0; right: 0; top: 160px; height: 80px; gap: 22px; color: var(--card-white); font-size: 80px; }
  .wordmark--back .mark-square { width: 54px; height: 54px; background: var(--card-white); flex: none; }

  .person-name {
    position: absolute; left: 389px; top: 72px;
    color: var(--brand-green); font-weight: 700; font-size: 26px; letter-spacing: 0.2px;
  }
  .person-title {
    position: absolute; left: 389px; top: 107px;
    color: var(--text); font-weight: 500; font-size: 17px;
  }
  .divider { position: absolute; left: 387px; top: 136px; right: 0; height: 3px; background: var(--ink); }
  .contact-list { position: absolute; left: 389px; top: 148px; list-style: none; }
  .contact-item {
    display: flex; align-items: flex-start; gap: 10px;
    color: var(--text); font-size: 16.5px; line-height: 23px; font-weight: 500;
    margin-bottom: 10px;
  }
  .contact-item svg { width: 22px; height: 22px; flex: none; margin-top: 1px; fill: var(--brand-green); }
</style>
</head>
<body>
<main class="stage">
  <section class="card card--front" aria-label="Card front">
    <div class="wordmark wordmark--front">
      <span class="mark-square"></span>
      <span class="wordmark-name">RIDGELINE</span>
    </div>

    <h1 class="person-name">MY NAME IS COOL</h1>
    <p class="person-title">PRINCIPAL</p>
    <div class="divider"></div>

    <ul class="contact-list">
      <li class="contact-item">
        <svg viewBox="0 0 24 24" aria-hidden="true"><path d="M2 9c0-3 20-3 20 0v2h-5V9.5H7V11H2z M6 12h12l2 8H4z"/></svg>
        <span>(XXX)XXX-XXXX-Office<br>(XXX)XXX-XXXX-Mobile</span>
      </li>
      <li class="contact-item">
        <svg viewBox="0 0 24 24" aria-hidden="true"><path d="M3 6h18v12H3z M3 6l9 7 9-7" fill="none" stroke="#84c441" stroke-width="2"/></svg>
        <span>name@mydomain.com</span>
      </li>
      <li class="contact-item">
        <svg viewBox="0 0 24 24" aria-hidden="true"><path d="M12 2a7 7 0 0 0-7 7c0 5 7 13 7 13s7-8 7-13a7 7 0 0 0-7-7zm0 10a3 3 0 1 1 0-6 3 3 0 0 1 0 6z"/></svg>
        <span>My Address Rd.<br>Any City, ST 00000</span>
      </li>
      <li class="contact-item">
        <svg viewBox="0 0 24 24" aria-hidden="true"><circle cx="12" cy="12" r="9"/></svg>
        <span>www.mydomain.com</span>
      </li>
    </ul>
  </section>

  <section class="card card--back" aria-label="Card back">
    <div class="wordmark wordmark--back">
      <span class="mark-square"></span>
      <span class="wordmark-name">RIDGELINE</span>
    </div>
  </section>
</main>
</body>
</html>
```